Medical VIP club - small design

Please read the specs in a design brief attached. Also we don't have logo in a Vector format and attaching the only version we have.

Club

```html
<!DOCTYPE html>
<html lang="en">
<head>
<meta charset="utf-8">
<title>Mediveri – VIP Club</title>
<link rel="stylesheet" href="https://fonts.googleapis.com/css2?family=Cinzel:wght@400;600&family=Tinos:wght@700&display=swap">
<style>
  :root {
    --bg-brown: #4a3a2e;
    --band-light: #57473a;
    --panel: rgba(112, 90, 62, 0.88);
    --nav-text: #cbc1b0;
    --nav-accent: #a08a68;
    --heading: #d6ccbb;
    --body-text: #c9bda8;
    --rule: #3e3226;
    --frame: #3a3029;
    --watermark: rgba(255, 255, 255, 0.05);
    --social: #9b9189;
  }
  * { margin: 0; padding: 0; box-sizing: border-box; }
  html, body { width: 1200px; height: 900px; overflow: hidden; background: var(--bg-brown); }
  .canvas { position: relative; width: 1200px; height: 900px; overflow: hidden; background: var(--bg-brown); font-family: "Cinzel", "Times New Roman", serif; }

  .hero-photo {
    position: absolute; left: 0; top: 170px; width: 1200px; height: 557px;
    background:
      radial-gradient(ellipse 260px 120px at 820px 560px, rgba(220, 210, 200, 0.35), transparent 70%),
      linear-gradient(90deg, #3b3a33 0%, #3f3d36 40%, #5a5650 62%, #4d4a45 78%, #6b6660 90%, #3f3c38 100%);
  }
  .header-shape { position: absolute; left: 0; top: 0; width: 1200px; height: 240px; }

  .brand-watermark {
    position: absolute; left: 380px; top: 8px; font-size: 150px; font-weight: 400;
    color: var(--watermark); letter-spacing: 2px; white-space: nowrap; line-height: 1;
  }

  .main-nav { position: absolute; left: 0; top: 128px; width: 1200px; height: 26px; }
  .nav-item {
    position: absolute; top: 0; font-size: 17px; font-weight: 600; letter-spacing: 1.6px;
    color: var(--nav-text); white-space: nowrap;
  }
  .nav-item--vip { color: var(--nav-accent); }
  .nav-item--vip::before {
    content: ""; position: absolute; left: -26px; top: 3px; width: 14px; height: 14px;
    border-radius: 50%; background: var(--nav-accent);
  }
  .registration-ornament {
    position: absolute; left: 786px; top: 106px; width: 186px; height: 66px;
    border-radius: 33px; background: rgba(160, 138, 104, 0.18);
  }

  .news-panel {
    position: absolute; left: 44px; top: 232px; width: 616px; height: 454px;
    background: var(--panel); box-shadow: 0 2px 10px rgba(0, 0, 0, 0.35);
  }
  .news-title {
    position: absolute; left: 0; top: 28px; width: 600px; text-align: center;
    font-size: 25px; font-weight: 600; letter-spacing: 1px; color: var(--heading);
  }
  .title-ornament {
    position: absolute; left: 203px; top: 56px; width: 196px; height: 44px;
    background: linear-gradient(180deg, rgba(62, 48, 36, 0.7), rgba(62, 48, 36, 0.35));
    border-radius: 4px;
  }
  .news-body {
    position: absolute; left: 76px; top: 114px; width: 462px; text-align: center;
    font-family: "Tinos", "Times New Roman", serif; font-weight: 700;
    font-size: 15.5px; line-height: 22.5px; letter-spacing: 1px; color: var(--body-text);
    word-break: break-all;
  }
  .news-rule {
    position: absolute; left: 192px; top: 268px; width: 232px; height: 2px; background: var(--rule);
  }
  .news-photo {
    position: absolute; top: 293px; width: 190px; height: 127px;
    border: 5px solid var(--frame);
    background: radial-gradient(ellipse 40px 60px at 50% 45%, #e8c27a, #b47a3c 60%, #5a3820 100%);
  }
  .news-photo--one { left: 101px; }
  .news-photo--two { left: 329px; }

  .service-tile {
    position: absolute; top: 791px; height: 56px;
    box-shadow: 0 2px 6px rgba(0, 0, 0, 0.4);
  }
  .service-tile--emergency { left: 78px; width: 90px; background: linear-gradient(90deg, #5a4a3c, #7a6852); }
  .service-tile--travel { left: 196px; width: 91px; background: linear-gradient(180deg, #d8cdbc, #8a7a66); }
  .service-tile--reception { left: 320px; width: 90px; background: linear-gradient(90deg, #5b4a3a, #b8a488, #5b4a3a); }
  .service-tile--staff { left: 437px; width: 93px; background: linear-gradient(180deg, #c9b89c, #8d7a60); }
  .service-tile--partners { left: 558px; width: 90px; background: linear-gradient(135deg, #4e3f33, #a89478, #4e3f33); }

  .brand-lockup { position: absolute; left: 772px; top: 796px; width: 210px; }
  .brand-name {
    display: block; font-size: 32px; font-weight: 600; color: #8b7658; letter-spacing: 0.5px; line-height: 1;
  }
  .brand-tagline {
    display: block; margin-top: 8px; font-size: 12px; font-weight: 600; color: #8b7658; letter-spacing: 1px;
  }

  .social-links { position: absolute; left: 1072px; top: 850px; display: flex; gap: 10px; }
  .social-square { width: 28px; height: 28px; border-radius: 4px; background: var(--social); }
</style>
</head>
<body>
<div class="canvas">
  <div class="hero-photo" role="img" aria-label="Photograph of a calm spa room with stone wall tiles, mosaic column, dark bowl and candles on a wooden bench"></div>

  <svg class="header-shape" viewBox="0 0 1200 240" aria-hidden="true">
    <path d="M0,0 H1200 V172 C1000,178 820,222 600,214 C380,206 200,196 0,204 Z" fill="#4a3a2e"/>
    <path d="M60,0 C300,40 700,40 1000,0 Z" fill="#57473a"/>
  </svg>

  <div class="brand-watermark" aria-hidden="true">mediveri</div>

  <div class="registration-ornament" role="img" aria-label="Decorative scroll ornament framing the registration link"></div>

  <nav class="main-nav">
    <span class="nav-item" style="left:40px">ABOUT US</span>
    <span class="nav-item nav-item--vip" style="left:205px">VIP CLUB</span>
    <span class="nav-item" style="left:368px">SERVICES</span>
    <span class="nav-item" style="left:528px">PACKAGES &amp; PRICES</span>
    <span class="nav-item" style="left:801px">REGISTRATION</span>
    <span class="nav-item" style="left:1034px">CONTACT</span>
  </nav>

  <section class="news-panel">
    <h1 class="news-title">NEW HOTEL</h1>
    <div class="title-ornament" role="img" aria-label="Decorative flourish under the heading"></div>
    <p class="news-body">Blahblah blahblaah blah blah. Blahblah blahblaah blah blah.Blahblah blahblaah blah blah.Blah blah blahblaah blah blah.Blahblah blahblaah blaah blah blah.Blahblah blahblaah blah blah.Blah blah blahblaah blah blah.Blahblah blahblaah bla blah.Blahblah blahblaah blah blah.</p>
    <div class="news-rule"></div>
    <div class="news-photo news-photo--one" role="img" aria-label="Photograph of a warmly lit hotel lobby corridor with arches and a chandelier"></div>
    <div class="news-photo news-photo--two" role="img" aria-label="Photograph of a warmly lit hotel lobby corridor with arches and a chandelier"></div>
  </section>

  <div class="service-tile service-tile--emergency" role="img" aria-label="Photograph of an emergency direction sign"></div>
  <div class="service-tile service-tile--travel" role="img" aria-label="Photograph of an airplane at an airport"></div>
  <div class="service-tile service-tile--reception" role="img" aria-label="Photograph of a hotel reception bell"></div>
  <div class="service-tile service-tile--staff" role="img" aria-label="Photograph of a medical team"></div>
  <div class="service-tile service-tile--partners" role="img" aria-label="Photograph of a handshake"></div>

  <div class="brand-lockup">
    <span class="brand-name">mediveri</span>
    <span class="brand-tagline">Клиника Медивери</span>
  </div>

  <div class="social-links">
    <span class="social-square" aria-label="Social network link"></span>
    <span class="social-square" aria-label="Social network link"></span>
    <span class="social-square" aria-label="News feed link"></span>
  </div>
</div>
</body>
</html>
```